Webdesign für Projektmanagement
Zielgruppe
Projektmanagement und Projektsteuerung von Bauvorhaben für Projektentwickler und Bauträger.
Wesentliche Bereiche sind Wirtschaftliche Steuerung, Steuerung der Baustelle und Bauabläufe sowie Steuerung der Marketing und Vertriebsaktivitäten.
Aufgabenstellung
Orientierung am Logo. Logo und Visitenkarte liegen bei. Schriftart Prelo und Prelo Slab.

```html
<!DOCTYPE html>
<html lang="de">
<head>
<meta charset="utf-8">
<title>Halbach Real Estate</title>
<link rel="stylesheet" href="https://fonts.googleapis.com/css2?family=Roboto+Condensed:wght@300;400;700&family=Roboto:wght@400&family=Roboto+Slab:wght@700&display=swap">
<style>
:root{
  --navy:#03243f;
  --navy-deep:#021a2f;
  --gold:#8a7a3c;
  --gold-text:#a8944a;
  --white:#ffffff;
  --cream:#f3efe4;
  --nav-text:#1c2b3a;
}
*{margin:0;padding:0;box-sizing:border-box}
html,body{width:1200px;height:1200px;overflow:hidden;background:var(--white)}
body{font-family:"Roboto Condensed",sans-serif;position:relative}

.site-header{position:absolute;top:0;left:0;width:1200px;height:90px;background:var(--white)}
.brand{position:absolute;left:149px;top:30px;font-family:"Roboto Slab",serif;font-weight:700;font-size:27px;line-height:1;color:var(--navy);letter-spacing:-.3px}
.main-nav{position:absolute;right:150px;top:0;height:90px;display:flex;gap:22px}
.main-nav a{position:relative;display:block;height:90px;padding-top:56px;font-size:13.5px;color:var(--nav-text);text-decoration:none;text-transform:uppercase;font-weight:400}
.main-nav a.is-active{color:var(--gold-text)}
.main-nav a.is-active::after{content:"";position:absolute;left:-3px;right:-3px;bottom:0;height:3px;background:var(--gold)}

.hero{position:absolute;top:90px;left:0;width:1200px;height:535px;overflow:hidden}
.hero-photo{position:absolute;inset:0;background:
  linear-gradient(180deg,rgba(8,20,34,.15) 0%,rgba(8,20,34,0) 40%,rgba(8,20,34,.35) 100%),
  linear-gradient(180deg,#27384b 0%,#4c4a46 35%,#6b5a3c 55%,#3c3a36 70%,#1f2a36 100%)}
.hero-title{position:absolute;left:0;right:0;text-align:center;color:var(--cream);text-transform:uppercase;font-weight:400;line-height:1}
.hero-title .line-1{position:absolute;left:0;right:0;top:160px;font-size:63px;letter-spacing:.5px}
.hero-title .line-2{position:absolute;left:0;right:0;top:222px;font-size:96px;letter-spacing:1px}
.scroll-down{position:absolute;left:576px;top:434px;width:48px;height:48px}

.about{position:absolute;top:625px;left:0;width:1200px;height:521px;background:var(--navy)}
.about-heading{position:absolute;top:82px;left:0;right:0;text-align:center;color:var(--white);font-size:40px;font-weight:300;text-transform:uppercase;letter-spacing:.3px}
.about-heading strong{font-weight:700}
.services{position:absolute;top:180px;left:150px;width:900px;display:flex}
.service{width:300px;text-align:center;display:flex;flex-direction:column;align-items:center}
.service-icon{width:50px;height:48px}
.service-title{margin-top:28px;color:var(--gold-text);font-size:22px;font-weight:400;text-transform:uppercase;letter-spacing:.2px}
.service-text{margin-top:8px;font-family:"Roboto",sans-serif;color:var(--white);font-size:11px;line-height:16.5px;width:285px}
.btn{margin-top:40px;display:block;width:150px;height:33px;line-height:33px;background:var(--gold);color:var(--white);font-size:11px;text-transform:uppercase;text-decoration:none}

.site-footer{position:absolute;top:1146px;left:0;width:1200px;height:54px;background:var(--gold);color:var(--white);font-size:10px;text-transform:uppercase}
.copyright{position:absolute;left:149px;top:21px}
.footer-nav{position:absolute;right:150px;top:21px;display:flex;gap:19px}
.footer-nav a{color:var(--white);text-decoration:none}
</style>
</head>
<body>
<header class="site-header">
  <div class="brand">Halbach Real Estate</div>
  <nav class="main-nav">
    <a href="#" class="is-active">Start</a>
    <a href="#">Leistungen</a>
    <a href="#">Über uns</a>
    <a href="#">Referenzen</a>
    <a href="#">Kontakt</a>
  </nav>
</header>

<section class="hero">
  <div class="hero-photo" role="img" aria-label="Abendliche Hafenszene mit geschwungenen modernen Gebäuden und Booten im Wasser"></div>
  <h1 class="hero-title">
    <span class="line-1">Wir gestalten</span>
    <span class="line-2">Lebensraum</span>
  </h1>
  <svg class="scroll-down" viewBox="0 0 48 48" aria-hidden="true">
    <circle cx="24" cy="24" r="22.5" fill="rgba(0,0,0,.15)" stroke="#a8944a" stroke-width="1.5"/>
    <polyline points="17,21 24,28 31,21" fill="none" stroke="#a8944a" stroke-width="1.5"/>
  </svg>
</section>

<section class="about">
  <h2 class="about-heading">Über <strong>Halbach</strong> Real Estate</h2>
  <div class="services">
    <div class="service">
      <svg class="service-icon" viewBox="0 0 50 48" fill="none" stroke="#fff" stroke-width="1.2" aria-hidden="true">
        <rect x="1" y="8" width="48" height="38" rx="1.5"/>
        <path d="M18 8V3h14v5M19 8V4.5h12V8"/>
        <path d="M1 21h48"/>
        <rect x="22" y="19" width="6" height="5"/>
      </svg>
      <h3 class="service-title">Projektmanagement</h3>
      <p class="service-text">Lorem ipsum dolor sit amet, consetetur sadipscing elitr, sed diam nonumy eirmod tempor invidunt ut labore et dolore magna aliquyam erat, sed diam voluptua.</p>
      <a href="#" class="btn">Mehr erfahren</a>
    </div>
    <div class="service">
      <svg class="service-icon" viewBox="0 0 50 48" fill="none" stroke="#fff" stroke-width="1.2" aria-hidden="true">
        <rect x="4" y="1" width="34" height="42"/>
        <path d="M8 8h8M19 8h14M8 14h6M17 14h14M8 20h8M19 20h10"/>
        <path d="M31 47V31a2 2 0 0 1 4 0v8l7 2a3 3 0 0 1 2 3v3"/>
        <rect x="30" y="43" width="14" height="4"/>
      </svg>
      <h3 class="service-title">Projektsteuerung</h3>
      <p class="service-text">Lorem ipsum dolor sit amet, consetetur sadipscing elitr, sed diam nonumy eirmod tempor invidunt ut labore et dolore magna aliquyam erat, sed diam voluptua.</p>
      <a href="#" class="btn">Mehr erfahren</a>
    </div>
    <div class="service">
      <svg class="service-icon" viewBox="0 0 50 48" fill="none" stroke="#fff" stroke-width="1.2" aria-hidden="true">
        <path d="M4 17h6v12H4z"/>
        <path d="M10 18l34-12v34L10 28"/>
        <path d="M44 5v36"/>
        <path d="M20 31l2 8h10l-1-5"/>
      </svg>
      <h3 class="service-title">Marketing &amp; Vertrieb</h3>
      <p class="service-text">Lorem ipsum dolor sit amet, consetetur sadipscing elitr, sed diam nonumy eirmod tempor invidunt ut labore et dolore magna aliquyam erat, sed diam voluptua.</p>
      <a href="#" class="btn">Mehr erfahren</a>
    </div>
  </div>
</section>

<footer class="site-footer">
  <div class="copyright">© 2017 Halbach Real Estate GmbH</div>
  <nav class="footer-nav">
    <a href="#">Partner</a>
    <a href="#">Kontakt</a>
    <a href="#">Impressum</a>
  </nav>
</footer>
</body>
</html>
```